Membership Based Medical Practice Website

We need a functioning website for a new Membership based medical practice. There will be an enrollment fee and a monthly fee. We would like to see designs that are modern, simple. Should use neutral light colors. Examples of sites we like are www.kellanmoorclinic.com and https://fernholtcare.com/ We also have a link that when "Join Now" is clicked it will go to the signup website.

Target Market(s)

Gay Men, local population, Age group 20 to 60's.

Industry/Entity Type

Medical

Coding

Coded - Design and coding required

Number of Pages Required

5+ page

Font styles to use
Sans Serif

Colors
ffffff
cee9f5
ecf7fb
cfeae6
edf8f6
aaaaaa
e9e9e9
dbdbdb
fff3d1

Requirements
Must have
• Logo and header on every page. Clean, simple design, clear content, mobile compatible.
• Must use Wordpress
Nice to have
• Ideas should come from kellanmoorclinic.com
• Easy to read
Should not have
• Generic patient pictures, bold colors.
• Should not copy from above websites.

```html
<!DOCTYPE html>
<html lang="en">
<head>
<meta charset="utf-8">
<title>Larkmere Infectious Disease Specialists</title>
<link rel="stylesheet" href="https://fonts.googleapis.com/css2?family=Questrial&family=Roboto:wght@400;500;700&display=swap">
<style>
:root{
  --white:#ffffff;
  --ink:#1c1c1c;
  --text:#3a3a3a;
  --muted:#6f6f6f;
  --gold:#d6a84a;
  --cream:#fff3d1;
  --mint:#cfeae6;
  --sky:#ecf7fb;
  --line:#dbdbdb;
  --footer:#e9e9e9;
  --card-border:#dbdbdb;
}
*{box-sizing:border-box;margin:0;padding:0}
html,body{width:1200px;height:2965px;overflow:hidden;background:var(--white)}
body{font-family:"Roboto",sans-serif;color:var(--text);position:relative}
.abs{position:absolute}
h1,h2{font-family:"Questrial",sans-serif;font-weight:400;color:var(--ink)}

/* header */
.site-header{position:absolute;left:0;top:0;width:1200px;height:155px;background:var(--white)}
.brand{position:absolute;left:112px;top:34px;display:flex;align-items:center;gap:12px}
.brand-dot{width:26px;height:26px;border-radius:50%;background:var(--gold)}
.brand-name{font-family:"Roboto",sans-serif;font-weight:500;color:#2b2b2b;line-height:1.25}
.brand-name .big{display:block;font-size:19px;letter-spacing:7px}
.brand-name .small{display:block;font-size:10.5px;letter-spacing:.2px}
.main-nav{position:absolute;left:415px;top:68px;display:flex;gap:0}
.main-nav a{font-family:"Roboto",sans-serif;font-weight:500;font-size:17px;color:var(--ink);text-decoration:none;position:absolute;white-space:nowrap}
.join-btn{position:absolute;left:955px;top:54px;width:135px;height:48px;border-radius:24px;background:var(--cream);box-shadow:0 2px 6px rgba(0,0,0,.15);font-weight:500;font-size:17px;color:var(--ink);display:flex;align-items:center;justify-content:center}

/* hero */
.hero{position:absolute;left:0;top:155px;width:1200px;height:559px;background:linear-gradient(180deg,#cfd3d4 0%,#a9afae 30%,#5d6a52 52%,#3c4532 62%,#2c2c2c 80%,#222 100%)}
.hero-title{position:absolute;left:0;top:248px;width:1200px;text-align:center;font-family:"Questrial",sans-serif;font-size:38px;line-height:60px;color:var(--white);text-shadow:0 2px 6px rgba(0,0,0,.4)}
.hero-title b{font-weight:700;font-family:"Roboto",sans-serif}
.slide-arrow{position:absolute;width:44px;height:44px;border-radius:50%;background:#1d1d1d;display:flex;align-items:center;justify-content:center}

/* specialties */
.section-title{position:absolute;left:0;width:1200px;text-align:center;font-size:38px;line-height:56px}
.section-sub{position:absolute;left:0;width:1200px;text-align:center;font-size:17px;color:var(--text)}
.spec-list{position:absolute;list-style:none;font-size:15.5px;color:var(--text)}
.spec-list li{height:37px;display:flex;align-items:center;gap:12px}
.chev{color:var(--gold);font-size:15px;letter-spacing:-2px}
.divider{position:absolute;left:112px;top:1230px;width:976px;height:1px;background:var(--line)}

/* features */
.feature-card{position:absolute;top:1466px;width:217px;height:242px;border:1px solid var(--card-border);background:var(--white);text-align:center;padding-top:22px}
.feature-card.active{background:var(--mint);border-color:var(--mint)}
.feature-card svg{display:block;margin:0 auto}
.feature-card h3{font-family:"Roboto",sans-serif;font-weight:700;font-size:19.5px;color:#2a2a2a;margin-top:14px}
.feature-card p{font-size:14px;line-height:25px;color:var(--muted);margin:8px 14px 0}
.feature-card.active p{color:#5c6e6b}
.side-arrow{position:absolute;top:1572px}

/* pricing */
.pricing{position:absolute;left:0;top:1837px;width:1200px;height:683px;background:var(--sky)}
.price-list{position:absolute;left:112px;top:2142px;list-style:none;font-size:14.5px;color:var(--text)}
.price-list li{height:37.5px;display:flex;align-items:center;gap:16px}
.learn-btn{position:absolute;left:112px;top:2357px;width:284px;height:50px;border-radius:25px;background:var(--cream);box-shadow:0 2px 6px rgba(0,0,0,.15);font-weight:500;font-size:17px;color:var(--ink);display:flex;align-items:center;justify-content:center;gap:6px}
.price-photo{position:absolute;left:665px;top:2146px;width:424px;height:263px;border:3px solid var(--white);box-shadow:0 1px 5px rgba(0,0,0,.2);background:linear-gradient(180deg,#f2d6b8 0%,#f7c98f 40%,#e9a25a 70%,#8a6b4a 100%)}

/* footer */
.site-footer{position:absolute;left:0;top:2520px;width:1200px;height:445px;background:var(--footer)}
.footer-brand{position:absolute;left:112px;top:2690px;display:flex;align-items:center;gap:14px}
.footer-brand .big{font-size:22px;letter-spacing:12px}
.footer-brand .small{font-size:13px}
.footer-col h4{position:absolute;font-family:"Roboto",sans-serif;font-weight:500;font-size:18px;color:var(--ink)}
.footer-links{position:absolute;list-style:none;font-size:14.5px;color:var(--text)}
.footer-links li{height:37px;display:flex;align-items:center;gap:14px}
.contact-item{position:absolute;left:475px;display:flex;gap:16px;font-size:14.5px;line-height:26px;color:var(--text)}
.social-line{position:absolute;top:2857px;height:1px;background:#9a9a9a}
.social{position:absolute;top:2837px;width:40px;height:40px;border-radius:50%}
.copyright{position:absolute;left:0;top:2908px;width:1200px;text-align:center;font-size:15px;color:var(--text)}
</style>
</head>
<body>

<header class="site-header">
  <div class="brand">
    <span class="brand-dot"></span>
    <span class="brand-name"><span class="big">LARKMERE</span><span class="small">INFECTIOUS DISEASE SPECIALISTS</span></span>
  </div>
  <nav class="main-nav">
    <a style="left:0">HOME</a>
    <a style="left:75px">SPECIALTIES</a>
    <a style="left:202px">PRICING</a>
    <a style="left:295px">ABOUT US</a>
    <a style="left:402px">FAQ</a>
    <a style="left:459px">BLOG</a>
  </nav>
  <div class="join-btn">JOIN US</div>
</header>

<section class="hero" role="img" aria-label="Photo of an empty road running through green misty hills"></section>
<div class="hero-title">Specialty <b>MEDICINE WITH</b> Commitment,<br>Compassion and <b>CARE</b></div>
<div class="slide-arrow" style="left:42px;top:411px"><svg width="14" height="14" viewBox="0 0 14 14"><path d="M9 2 4 7l5 5" fill="none" stroke="#fff" stroke-width="2"/></svg></div>
<div class="slide-arrow" style="left:1114px;top:411px"><svg width="14" height="14" viewBox="0 0 14 14"><path d="M5 2l5 5-5 5" fill="none" stroke="#fff" stroke-width="2"/></svg></div>

<h2 class="section-title" style="top:808px">We Offer Comprehensive Treatment Of A Wide<br>Variety Of Infectious Diseases</h2>
<p class="section-sub" style="top:965px">Out Expertise Is In The Following Area.</p>
<ul class="spec-list" style="left:112px;top:1027px">
  <li><span class="chev">»</span>HIV/PrEP</li>
  <li><span class="chev">»</span>Chronic Hepatitis</li>
  <li><span class="chev">»</span>Sexually transmitted infections</li>
</ul>
<ul class="spec-list" style="left:412px;top:1027px">
  <li><span class="chev">»</span>Bone and Joint infections</li>
  <li><span class="chev">»</span>Postsurgical infections</li>
  <li><span class="chev">»</span>Pre-travel vaccinations &amp; counselling</li>
</ul>
<ul class="spec-list" style="left:745px;top:1027px">
  <li><span class="chev">»</span>Tuberculosis</li>
  <li><span class="chev">»</span>Diabetes related infections</li>
  <li><span class="chev">»</span>Infections associated with medical devices</li>
</ul>
<div class="divider"></div>

<h2 class="section-title" style="top:1320px">Less Wait, More Personal</h2>
<p class="section-sub" style="top:1393px">We are not your traditional doctor's office.</p>

<svg class="side-arrow" style="left:58px" width="18" height="30" viewBox="0 0 18 30"><path d="M15 2 3 15l12 13" fill="none" stroke="#666" stroke-width="2.5"/></svg>
<svg class="side-arrow" style="left:1124px" width="18" height="30" viewBox="0 0 18 30"><path d="M3 2l12 13-12 13" fill="none" stroke="#666" stroke-width="2.5"/></svg>

<article class="feature-card" style="left:112px">
  <svg width="72" height="60" viewBox="0 0 72 60" fill="none" stroke="#666" stroke-width="2">
    <path d="M36 30c-8-7-14-11-14-17a7 7 0 0 1 14-2 7 7 0 0 1 14 2c0 6-6 10-14 17z"/>
    <path d="M6 20v18l14 14v6M66 20v18L52 52v6M12 30l10 10M60 30 50 40"/>
  </svg>
  <h3>Devoted Care</h3>
  <p>We schedule enough time at each visit to make sure all of your questions are answered.</p>
</article>
<article class="feature-card active" style="left:365px">
  <svg width="72" height="60" viewBox="0 0 72 60" fill="none" stroke="#d6a84a" stroke-width="2">
    <path d="M36 50S22 34 22 22a14 14 0 0 1 28 0c0 12-14 28-14 28z"/>
    <circle cx="36" cy="22" r="6"/>
    <ellipse cx="36" cy="53" rx="16" ry="4"/>
  </svg>
  <h3>Within Your Reach</h3>
  <p>We schedule enough time at each visit to make sure all of your questions are answered.</p>
</article>
<article class="feature-card" style="left:618px">
  <svg width="72" height="60" viewBox="0 0 72 60" fill="none" stroke="#666" stroke-width="2">
    <circle cx="40" cy="18" r="11"/>
    <path d="M40 11v14M36 14h6a2.5 2.5 0 0 1 0 5h-4a2.5 2.5 0 0 0 0 5h6"/>
    <path d="M8 44l12-8h14l8 4H28M8 52l10-4 22 2 20-14"/>
  </svg>
  <h3>Save on Lab Costs</h3>
  <p>We schedule enough time at each visit to make sure all of your questions are answered.</p>
</article>
<article class="feature-card" style="left:872px">
  <svg width="72" height="60" viewBox="0 0 72 60" fill="none" stroke="#666" stroke-width="2">
    <circle cx="36" cy="10" r="5"/><path d="M28 24a8 8 0 0 1 16 0"/>
    <path d="M36 26v8M18 34h36M18 34v6M36 34v6M54 34v6"/>
    <circle cx="18" cy="45" r="4"/><circle cx="36" cy="45" r="4"/><circle cx="54" cy="45" r="4"/>
    <path d="M11 57a7 7 0 0 1 14 0M29 57a7 7 0 0 1 14 0M47 57a7 7 0 0 1 14 0"/>
  </svg>
  <h3>No Middle Man</h3>
  <p>We schedule enough time at each visit to make sure all of your questions are answered.</p>
</article>

<section class="pricing"></section>
<h2 class="section-title" style="top:1934px">Our Pricing is Simple, Transparent<br>And Affordable.</h2>
<p class="section-sub" style="top:2059px;font-weight:500">Membership Plan $80/mo, plus a one-time $99 enrollment fee.</p>
<ul class="price-list">
  <li><span class="chev">»</span>Includes all appointments, no co-pay</li>
  <li><span class="chev">»</span>Relaxed, unrushed visits</li>
  <li><span class="chev">»</span>Direct communication with your doctor via phone, email, video chat 24/7</li>
  <li><span class="chev">»</span>Convenient online scheduling (no need to call during business hours)</li>
  <li><span class="chev">»</span>Wholesale price for labs and medications</li>
</ul>
<div class="learn-btn">LEARN MORE ABOUT US
  <svg width="16" height="16" viewBox="0 0 16 16"><circle cx="8" cy="8" r="8" fill="#1c1c1c"/><path d="M6.5 4.5 10 8l-3.5 3.5" fill="none" stroke="#fff" stroke-width="2"/></svg>
</div>
<div class="price-photo" role="img" aria-label="Photo of a group of friends seen from behind, arms around each other at sunset"></div>

<footer class="site-footer"></footer>
<div class="footer-brand brand-name">
  <span class="brand-dot" style="width:32px;height:32px;border-radius:50%;background:var(--gold)"></span>
  <span><span class="big">LARKMERE</span><span class="small">INFECTIOUS DISEASE SPECIALISTS</span></span>
</div>

<div class="footer-col"><h4 style="left:475px;top:2610px">CONTACT US</h4></div>
<div class="contact-item" style="top:2658px">
  <svg width="14" height="20" viewBox="0 0 14 20" style="margin-top:4px"><path d="M7 0a7 7 0 0 1 7 7c0 5-7 13-7 13S0 12 0 7a7 7 0 0 1 7-7z" fill="#d6a84a"/><circle cx="7" cy="7" r="2.5" fill="#e9e9e9"/></svg>
  <span>123 Sample Street, Sample City,<br>New State, USA.</span>
</div>
<div class="contact-item" style="top:2728px">
  <svg width="14" height="16" viewBox="0 0 14 16" style="margin-top:5px"><path d="M3 1l3 3-2 2c1 2 3 4 5 5l2-2 3 3-2 3C6 14 1 8 1 3z" fill="#d6a84a"/></svg>
  <span>(+1) 123 456 7890</span>
</div>
<div class="contact-item" style="top:2771px">
  <svg width="14" height="12" viewBox="0 0 14 12" style="margin-top:7px"><rect width="14" height="11" rx="1" fill="#d6a84a"/><path d="M1 1l6 5 6-5" fill="none" stroke="#e9e9e9" stroke-width="1.3"/></svg>
  <span>info@larkmereid.com</span>
</div>

<div class="footer-col"><h4 style="left:775px;top:2610px">QUICK LINKS</h4></div>
<ul class="footer-links" style="left:775px;top:2650px">
  <li><span class="chev">»</span>Home</li>
  <li><span class="chev">»</span>Specialties</li>
  <li><span class="chev">»</span>Pricing</li>
  <li><span class="chev">»</span>About Us</li>
</ul>
<div class="footer-col"><h4 style="left:980px;top:2610px">RESOURCES</h4></div>
<ul class="footer-links" style="left:980px;top:2650px">
  <li><span class="chev">»</span>Latest News</li>
  <li><span class="chev">»</span>Clients</li>
  <li><span class="chev">»</span>FAQs</li>
  <li><span class="chev">»</span>Conact Us</li>
</ul>

<div class="social-line" style="left:112px;width:362px"></div>
<div class="social-line" style="left:726px;width:362px"></div>
<span class="social" style="left:496px;background:#1f4e8c"></span>
<span class="social" style="left:551px;background:#1e9be0"></span>
<span class="social" style="left:606px;background:#d6157e"></span>
<span class="social" style="left:661px;background:#d21b1b"></span>

<p class="copyright">Copyright © 2019 Larkmere. All Rights Reserved &nbsp;|&nbsp; Privacy Policy.</p>

</body>
</html>
```